Flalzflyer-Design (Folder)
Da für uns neben einem guten Design ein angenehmer und konstruktiver Dialog sowie Verlässlichkeit von hoher Bedeutung ist, sind wir sehr froh auf dieser Plattform auf "brightloom" gestoßen zu sein. Wir sagen ganz herzlich DANKE!!
Zielgruppe
Zielgruppe im Bereich der Vermietung sind Alleinreisende oder als Paar verreisende Natur- und Nordsee verbundene Feriengäste (ü30) mit dem Urlaubsziel 'Sylt', welche eine persönlich und mit besonderem Schick eingerichtet Ferienwohnung/Ferienapartment in zentraler Lage in Westerland suchen und die es als positiven bzw. interessanten Aspekt sehen, dass die Ferienwohnungen direkt von uns Insulaner angeboten werden und wir als Sylter Familie ebenfalls Vor-Ort mit dem Urlaubern unter dem selben Dach leben (wenn auch nicht in der derselben Wohnung ;) ), ganz gemäß unserem Slogan 'Nordseeurlaub unter einem Dach mit Insulanern'
Aufgabenstellung
Es soll ein Falzflyer (Folder) mit Wickelfalz (siehe ggf. https://www.druckwerk-nord.de/werbemittel/folder.html) designed werden (4/4-farbig Euroskala). Bestehend aus einem Papier Format DIN A4 mit zwei Falzen, sodass sich bei Berücksichtigung von Vor- u. Rückseite 6 Seiten ergeben. Die wesentlichen Texte/Inhalte/Informationen, finden sich hier: https://www.quartiersuche-online.de/481926/ . Neben dem Ferienapartment 'Kompass' w ird von uns die Ferienwohnung 'Wadlen' (friesisch für Seestern) angeboten, ebenfalls im Morgenlicht Sylt HOUSE (EST. 2017).
Preisangaben können unberücksichtigt beliben, da sie dem Folder später über eine gesondere Einlage beigelegt werden sollen.
Im Rahmen des Dateiupload bei entwurfsmarkt werden nur einige der möglichen Fotos bereitgestellt. Sie sollen als Auswahlmöglichkeit dienen. Welche der Fotos Verwendung finden oder nach weiteren nachgefragt wird, soll in Abhängigkeit mit dem Gesamtdesign stehen und zunächst von Ihnen entschieden werden, um ein möglichst ansprechenden und harmonischen Folder kreieren zu können.

```html
<!DOCTYPE html>
<html lang="de">
<head>
<meta charset="utf-8">
<title>Morgenlicht Sylt HOUSE – Folder</title>
<link href="https://fonts.googleapis.com/css2?family=Lato:wght@400;700;900&family=Arimo:wght@400;700&family=Caveat:wght@400&display=swap" rel="stylesheet">
<style>
:root{
  --blue:#2b8fc0;
  --ink:#3f3f3f;
  --ink-soft:#555;
  --divider:#d6d9df;
  --paper:#ffffff;
}
*{margin:0;padding:0;box-sizing:border-box}
html,body{width:840px;height:1200px;overflow:hidden;background:var(--paper)}
.folder{position:relative;width:840px;height:1200px;font-family:'Lato',sans-serif;color:var(--ink)}
.photo{position:absolute}
.fold-line{position:absolute;left:0;top:597px;width:840px;height:5px;background:var(--divider)}
.script{font-family:'Caveat',cursive;font-weight:400;color:var(--blue);white-space:nowrap;line-height:1}
.visit-title{position:absolute;left:290px;top:256px;font-size:15.5px;line-height:20px;font-weight:700;color:#4a4a4a;letter-spacing:.1px}
.visit-title span{font-weight:400}
.visit-text{position:absolute;left:290px;top:308px;width:254px;font-size:8.9px;line-height:13.8px;color:var(--ink-soft)}
.visit-text p+p{margin-top:13.8px}
.dash{position:absolute;left:290px;top:454px;width:251px;border-top:1px dashed var(--blue)}
.contact{position:absolute;left:290px;top:462px;width:265px;font-size:8.9px;line-height:12.8px;color:var(--ink-soft);white-space:nowrap}
.contact b{color:#444}
.contact .gap{height:10px}
.house-name{position:absolute;left:569px;top:405px;width:257px;text-align:center;font-weight:900;font-size:22px;color:#4a4a4a;letter-spacing:-.2px;white-space:nowrap}
.house-est{position:absolute;left:569px;top:430px;width:257px;text-align:center;font-size:10.5px;color:#555}
.slogan{position:absolute;left:569px;top:480px;width:257px;text-align:center;font-size:28px}
.tagline{position:absolute;left:569px;top:519px;width:257px;text-align:center;font-size:9.5px;line-height:13px;color:#444}
.tagline b{font-weight:700}
.apt-title{position:absolute;font-size:27px;top:622px}
.apt-lead,.apt-body{position:absolute;font-family:'Arimo',sans-serif;font-size:8.5px;line-height:12.8px;color:var(--ink)}
.apt-body h3{font-size:8.5px;font-weight:700}
.apt-body p+p{margin-top:12.8px}
.north{position:absolute}
.amenities{position:absolute;top:1122px;display:flex;justify-content:space-between}
.amenity{width:50px;text-align:center;font-family:'Arimo',sans-serif;font-size:6.2px;line-height:8.4px;color:#555}
.amenity svg{display:block;margin:0 auto 3px}
.service-title{position:absolute;left:298px;top:1062px;font-size:28px}
.service-text{position:absolute;left:299px;top:1105px;width:250px;font-family:'Arimo',sans-serif;font-size:8.5px;line-height:12.8px;color:var(--ink)}
.service-text p+p{margin-top:12.8px}
</style>
</head>
<body>
<svg width="0" height="0" style="position:absolute">
  <defs>
    <symbol id="ico-wifi" viewBox="0 0 40 40">
      <circle cx="20" cy="20" r="18.5" fill="none" stroke="var(--blue)" stroke-width="2.2"/>
      <path d="M10 18a14 14 0 0 1 20 0M13.5 21.5a9 9 0 0 1 13 0M17 25a4 4 0 0 1 6 0" fill="none" stroke="var(--blue)" stroke-width="2.4" stroke-linecap="round"/>
      <circle cx="20" cy="28" r="1.8" fill="var(--blue)"/>
    </symbol>
    <symbol id="ico-nosmoke" viewBox="0 0 40 40">
      <circle cx="20" cy="20" r="18.5" fill="none" stroke="var(--blue)" stroke-width="2.2"/>
      <rect x="9" y="21" width="20" height="4" fill="var(--blue)"/>
      <rect x="30" y="21" width="2" height="4" fill="var(--blue)"/>
      <path d="M26 13c2 1 2 3 0 4M29 12c2 1.5 2 4 0 5.5" fill="none" stroke="var(--blue)" stroke-width="1.4"/>
      <line x1="9" y1="11" x2="31" y2="30" stroke="var(--blue)" stroke-width="2.6"/>
    </symbol>
    <symbol id="ico-chair" viewBox="0 0 40 40">
      <circle cx="20" cy="20" r="18.5" fill="none" stroke="var(--blue)" stroke-width="2.2"/>
      <path d="M12 29V15a8 6 0 0 1 16 0v14Z" fill="none" stroke="var(--blue)" stroke-width="1.8"/>
      <path d="M15 16v11M18 15v12M21 15v12M24 16v11" stroke="var(--blue)" stroke-width="1.2"/>
    </symbol>
    <symbol id="ico-dish" viewBox="0 0 40 40">
      <circle cx="20" cy="20" r="18.5" fill="none" stroke="var(--blue)" stroke-width="2.2"/>
      <rect x="11" y="11" width="18" height="18" rx="2" fill="none" stroke="var(--blue)" stroke-width="1.8"/>
      <line x1="11" y1="16" x2="29" y2="16" stroke="var(--blue)" stroke-width="1.4"/>
      <path d="M14 21c2 4 10 4 12 0" fill="none" stroke="var(--blue)" stroke-width="1.6"/>
    </symbol>
    <symbol id="ico-bed" viewBox="0 0 40 40">
      <circle cx="20" cy="20" r="18.5" fill="none" stroke="var(--blue)" stroke-width="2.2"/>
      <path d="M10 14v14M10 24h20v4M30 24v-4a3 3 0 0 0-3-3h-10v7" fill="none" stroke="var(--blue)" stroke-width="2"/>
      <circle cx="13.5" cy="19.5" r="2.2" fill="var(--blue)"/>
    </symbol>
    <symbol id="ico-tv" viewBox="0 0 40 40">
      <circle cx="20" cy="20" r="18.5" fill="none" stroke="var(--blue)" stroke-width="2.2"/>
      <rect x="10" y="12" width="20" height="13" rx="1.5" fill="none" stroke="var(--blue)" stroke-width="2"/>
      <path d="M16 29h8M20 25v4" stroke="var(--blue)" stroke-width="2"/>
    </symbol>
  </defs>
</svg>

<main class="folder">
  <!-- left panel, outside -->
  <div class="photo" style="left:14px;top:14px;width:124px;height:123px;background:linear-gradient(#5a85c4,#e9e7e2 55%,#3e4a35)" role="img" aria-label="Foto: Hausfassade mit Sprossenfenstern"></div>
  <div class="photo" style="left:141px;top:14px;width:121px;height:123px;background:linear-gradient(120deg,#7b2e2a,#b98e6a 60%,#d9d6d0)" role="img" aria-label="Foto: Dekoregal mit Sylt-Schriftzug"></div>
  <div class="photo" style="left:14px;top:140px;width:248px;height:174px;background:linear-gradient(160deg,#9db7d6 0%,#d8d3c4 45%,#c79a5a 75%,#8a6436)" role="img" aria-label="Foto: Dünenlandschaft mit Strand"></div>
  <div class="photo" style="left:14px;top:318px;width:78px;height:122px;background:linear-gradient(#3d6a66,#b39a6c 50%,#3a2b22)" role="img" aria-label="Foto: Wohnraum mit Fenster und Tisch"></div>
  <div class="photo" style="left:98px;top:318px;width:164px;height:122px;background:linear-gradient(150deg,#1f2226,#5f5147 55%,#9a8c7e)" role="img" aria-label="Foto: Holztisch mit Windlicht"></div>
  <div class="photo" style="left:14px;top:445px;width:248px;height:138px;background:linear-gradient(#8aa0b4,#e8b57a 45%,#f0a03c 55%,#2b2a28)" role="img" aria-label="Foto: Sonnenuntergang über dem Meer"></div>

  <!-- middle panel, back -->
  <div class="photo" style="left:290px;top:14px;width:251px;height:139px;background:linear-gradient(#a9c0d8,#3f5f78 35%,#e6dccb 55%,#d9cdb7)" role="img" aria-label="Foto: Strand mit Rettungsturm und Strandkörben"></div>
  <div class="photo" style="left:290px;top:156px;width:124px;height:85px;background:linear-gradient(120deg,#6b96d0,#c9a769 45%,#3d5a2c)" role="img" aria-label="Foto: Backsteinhaus mit Garten"></div>
  <div class="photo" style="left:417px;top:156px;width:124px;height:85px;background:linear-gradient(#2f6fc6,#5a64a6 40%,#3f6a36)" role="img" aria-label="Foto: Blühende Hortensien vor Klinkerbau"></div>

  <h2 class="visit-title">BESUCHEN SIE UNS<br><span>IN SYLT.</span></h2>
  <div class="visit-text">
    <p>Das Morgenlicht Sylt House (est. 2017) ist in Nachbarschaft des denkmalgeschützten Westerländer Polizeigebäudes (ehem. Amtsgericht) gelegen. Die vorteilhafte Lage ist damit zentral aber ruhig in 2. Reihe in Alt-Westerland.</p>
    <p>Der Bahnhof ist ca. 4-5 Gehminuten, die Fußgängerzone/Friedrichstr. mit div. Einkaufsmöglichkeiten und Restaurants/Cafés ca. 7 Min. und der Strand/die Kurpromenade ca. 12 Min. entfernt. Auch das Schwimmbad Dünenbad, das Inselvital Zentrum (Wellness) o. die Spielbank sind nah.</p>
  </div>
  <div class="dash"></div>
  <div class="contact">
    Familie Morgenlicht<br>
    <b>Morgenlicht Sylt HOUSE (EST. 2017)</b><br>
    Dünenstieg 14b, Westerland
    <div class="gap"></div>
    <b>Wir sind für Sie da</b> · &nbsp;Mo - So &nbsp;&nbsp;9.00 - 21.00<br>
    Telefon:+49 (0)4651 - 300 517 2 · Mobil: +49 (0)171 - 608 294 7<br>
    eMail: sylt@morgenlicht-haus.de<br>
    Web: quartiersuche-online.de/481926<br>
    Belegungskalender: belegung.morgenlicht-haus.de
  </div>

  <!-- right panel, cover -->
  <div class="photo" style="left:569px;top:14px;width:257px;height:376px;background:linear-gradient(#4f86c8 0%,#c7d8ec 30%,#2f5a6e 44%,#e4dccb 58%,#9c8460 80%,#6b5a40)" role="img" aria-label="Foto: Strand mit Strandkörben, Dünenzaun und Badeflagge"></div>
  <h1 class="house-name">Morgenlicht Sylt HOUSE</h1>
  <div class="house-est">(EST. 2017)</div>
  <div class="slogan script">Nordseeurlaub mit Insulanern</div>
  <p class="tagline">BEI UNS GIBT ES KEINE BEFREMDLICHE ANONYMITÄT,<br><b>SONDERN EIN HERZLICHES WILLKOMMEN!</b></p>

  <div class="fold-line"></div>

  <!-- inside left: Kompass -->
  <h2 class="apt-title script" style="left:14px">Ferienapartment 'Kompass'</h2>
  <div class="photo" style="left:14px;top:660px;width:127px;height:122px;background:linear-gradient(120deg,#8d8a84,#d6cfc4 45%,#8a5a36)" role="img" aria-label="Foto: Schlafzimmer mit Einzelbett"></div>
  <div class="photo" style="left:145px;top:660px;width:126px;height:122px;background:linear-gradient(150deg,#d8d4cc,#c9c4ba 45%,#3c3a3c)" role="img" aria-label="Foto: Wohnbereich mit Schlafsofa"></div>
  <p class="apt-lead" style="left:14px;top:792px;width:260px">Das Apartment ist seniorengerecht, ebenerdig, kurze Wege, Ansprechpartner im Haus, Bahnhof Westerland fussläufig 5 Min.</p>
  <svg class="north" style="left:17px;top:826px" width="22" height="26" viewBox="0 0 22 26"><text x="11" y="5" font-size="5" text-anchor="middle" fill="#333" font-family="Arimo,sans-serif">N</text><circle cx="11" cy="15" r="9" fill="none" stroke="#333" stroke-width=".8"/><path d="M11 6 L8 24 L11 18 L14 24Z" fill="none" stroke="#333" stroke-width=".8"/></svg>
  <div class="photo" style="left:52px;top:831px;width:208px;height:109px;background:linear-gradient(#eef2f5,#dfe7ee 70%,#fbf7dc)" role="img" aria-label="Grundriss des Apartments mit Schlafzimmer, Wohnbereich, Bad und Außenbereich mit Markise"></div>
  <div class="apt-body" style="left:14px;top:960px;width:262px">
    <h3>Wer Meer hat, braucht weniger, sagt man.</h3>
    <p>Die Zimmer persönlich und mit Geschick gestaltet, zeitgemäße Wohneinrichtung, modernes ebenerdiges Duschbad, hochwertige Pantryküche, Smart-TV, Wlan, ansprechendes und vollständiges Geschirr, Außenbereich sowie der persönlichen Nähe zu uns Insulanern.</p>
    <p>Das App. eignet sich für einen längeren Urlaub besonders für 1 Person. Es steht ein Einzelbett im kl. Schlafzimmer zur Verfügung. Für einen Aufenthalt von einigen Tagen haben 2 Pers. ebenfalls eine passend schöne Unterkunft (Schlafmöglichkeit auf komfortablen Schlafsofa mit Lattenrost).</p>
  </div>
  <div class="amenities" style="left:10px;width:254px">
    <div class="amenity"><svg width="38" height="38"><use href="#ico-wifi"/></svg>kostenloses<br>WLAN</div>
    <div class="amenity"><svg width="38" height="38"><use href="#ico-nosmoke"/></svg>Nichtraucher<br>Wohnung</div>
    <div class="amenity"><svg width="38" height="38"><use href="#ico-chair"/></svg>Strandkorb<br>vorhanden</div>
    <div class="amenity"><svg width="38" height="38"><use href="#ico-dish"/></svg>Geschirrspüler<br>vorhanden</div>
    <div class="amenity"><svg width="38" height="38"><use href="#ico-bed"/></svg>Bettwäsche &amp;<br>Handtücher</div>
  </div>

  <!-- inside middle: service -->
  <div class="photo" style="left:300px;top:616px;width:249px;height:299px;background:linear-gradient(100deg,#4a3a2e 0%,#7a6350 35%,#e9e9e6 60%,#f4f4f2 80%,#dcdcd8);" role="img" aria-label="Foto: Modernes Duschbad mit grünem Boden"></div>
  <div class="photo" style="left:299px;top:919px;width:78px;height:122px;background:linear-gradient(135deg,#b8b2a8,#d6d1c8 50%,#a9a398)" role="img" aria-label="Foto: Schriftzug im Sand"></div>
  <div class="photo" style="left:383px;top:919px;width:166px;height:122px;background:linear-gradient(#7fa7d6,#dce6ef 45%,#b9a98a 65%,#8c8a3e)" role="img" aria-label="Foto: Blick von der Düne auf Strand und Meer"></div>
  <h2 class="service-title script">Unser Service für Sie</h2>
  <div class="service-text">
    <p>Kostenloser Hol-/Bringservice Bahnhof Westerland nach Absprache möglich.</p>
    <p>Das Wäschepaket beinhaltet: Bettwäsche, Laken, Handtuch, Duschtuch, Badvorleger, Geschirrtuch.</p>
  </div>

  <!-- inside right: Wadlen -->
  <h2 class="apt-title script" style="left:577px">Ferienapartment 'Wadlen'</h2>
  <div class="photo" style="left:577px;top:660px;width:124px;height:122px;background:linear-gradient(#6b5a52,#d8d8dc 45%,#f1f0ec 70%,#c8473c)" role="img" aria-label="Foto: Schlafzimmer mit buntem Bettbezug"></div>
  <div class="photo" style="left:704px;top:660px;width:122px;height:122px;background:linear-gradient(120deg,#5a4a3c,#c9c1a8 55%,#e6e4de)" role="img" aria-label="Foto: Bad mit Fenster und Gräsern"></div>
  <p class="apt-lead" style="left:577px;top:792px;width:255px">Das Apartment ist seniorengerecht, ebenerdig, kurze Wege, Ansprechpartner im Haus, Bahnhof Westerland fussläufig.</p>
  <svg class="north" style="left:579px;top:826px" width="22" height="26" viewBox="0 0 22 26"><text x="11" y="5" font-size="5" text-anchor="middle" fill="#333" font-family="Arimo,sans-serif">N</text><circle cx="11" cy="15" r="9" fill="none" stroke="#333" stroke-width=".8"/><path d="M11 6 L8 24 L11 18 L14 24Z" fill="none" stroke="#333" stroke-width=".8"/></svg>
  <div class="photo" style="left:615px;top:832px;width:208px;height:109px;background:linear-gradient(#eef2f5,#dfe7ee 70%,#fbf7dc)" role="img" aria-label="Grundriss des Apartments mit Schlafzimmer, Wohnbereich, Bad und Außenbereich mit Markise"></div>
  <div class="apt-body" style="left:577px;top:960px;width:256px">
    <h3>Wer Meer hat, braucht weniger, sagt man.</h3>
    <p>Die Zimmer persönlich und mit Geschick gestaltet, zeitgemäße Wohneinrichtung, modernes ebenerdiges Duschbad, hochwertige Pantryküche, Smart-TV, Wlan, ansprechendes und vollständiges Geschirr, Außenbereich sowie der persönlichen Nähe zu uns Insulanern.</p>
    <p>Das App. eignet sich für einen längeren Urlaub besonders für 1 Person. Es steht ein Einzelbett im kl. Schlafzimmer zur Verfügung. Für einen Aufenthalt von einigen Tagen haben 2 Pers. ebenfalls eine passend schöne Unterkunft (Schlafmöglichkeit auf komfortablen Schlafsofa mit Lattenrost).</p>
  </div>
  <div class="amenities" style="left:573px;top:1116px;width:254px">
    <div class="amenity"><svg width="38" height="38"><use href="#ico-wifi"/></svg>kostenloses<br>WLAN</div>
    <div class="amenity"><svg width="38" height="38"><use href="#ico-nosmoke"/></svg>Nichtraucher<br>Wohnung</div>
    <div class="amenity"><svg width="38" height="38"><use href="#ico-tv"/></svg>Smart TV<br>vorhanden</div>
    <div class="amenity"><svg width="38" height="38"><use href="#ico-dish"/></svg>Geschirrspüler<br>vorhanden</div>
    <div class="amenity"><svg width="38" height="38"><use href="#ico-bed"/></svg>Bettwäsche &amp;<br>Handtücher</div>
  </div>
</main>
</body>
</html>
```